GlassHaven Artbook for Okanagan Region, British Columbia

Creating an art book: GlassHaven, for the Okanagan Wine Region in British Columbia, Canada. Would like smart, modern, clean and linear...cool, sexy urban, not ugly boring suburban... I need a cover that appeals to the wino in all of us! Title: GlassHaven -Marla Dovicki
Updates
Thank you all kindly for your efforts. I have added some files so that you can get a sense of my aesthetic...it's never easy trying to figure it out, is it? I will hopefully have dimensions of book soon...cheers, Marla
would anyone please design a giant wine bottle with the wine label that looks like a label but says glasshaven...just curious to see if it works as a design or not...thank you.
Target Market(s)
Designing this wine art book of quotes to wineries in Okanagan BC. Buyer is wine lover and tourist ready to spend his vacation bucks on this wonderful book!
Look and feel

```html
<!DOCTYPE html>
<html lang="en">
<head>
<meta charset="utf-8">
<title>GlassHaven — Book Cover</title>
<link rel="stylesheet" href="https://fonts.googleapis.com/css2?family=Roboto+Condensed:wght@700&family=Raleway:wght@400&display=swap">
<style>
  :root {
    --stage: #ffffff;
    --cover: #000000;
    --author: #8c7b68;
    --title: #c9b48e;
    --tone-slate: #5c6b7a;
    --tone-olive: #8c8662;
    --tone-wine: #6f4a48;
    --tone-grey: #6f716c;
    --tone-plum: #6c4a66;
    --tone-sky: #5f8198;
    --tone-violet: #4d4466;
  }
  * { margin: 0; padding: 0; box-sizing: border-box; }
  html, body {
    width: 1200px;
    height: 907px;
    overflow: hidden;
    background: var(--stage);
  }
  .canvas {
    position: relative;
    width: 1200px;
    height: 907px;
  }
  .book-cover {
    position: absolute;
    left: 350px;
    top: 44px;
    width: 500px;
    height: 820px;
    background: var(--cover);
    overflow: hidden;
  }
  .author-name {
    position: absolute;
    top: 74px;
    left: 36px;
    right: 0;
    text-align: center;
    font-family: "Raleway", sans-serif;
    font-weight: 400;
    font-size: 13px;
    letter-spacing: 0.95em;
    text-transform: uppercase;
    color: var(--author);
  }
  .bottle-artwork {
    position: absolute;
    left: 0;
    right: 0;
    top: 180px;
    height: 456px;
    background: linear-gradient(90deg,
      var(--tone-slate) 0%,
      var(--tone-olive) 14%,
      var(--tone-wine) 24%,
      var(--tone-grey) 36%,
      var(--tone-plum) 46%,
      var(--tone-olive) 56%,
      var(--tone-wine) 66%,
      var(--tone-grey) 76%,
      var(--tone-sky) 86%,
      var(--tone-violet) 100%);
    opacity: 0.85;
    -webkit-mask-image: linear-gradient(180deg, transparent 0%, #000 16%, #000 86%, transparent 100%);
            mask-image: linear-gradient(180deg, transparent 0%, #000 16%, #000 86%, transparent 100%);
  }
  .book-title {
    position: absolute;
    left: 0;
    top: 698px;
    font-family: "Roboto Condensed", sans-serif;
    font-weight: 700;
    font-size: 46px;
    line-height: 1;
    letter-spacing: -0.01em;
    color: var(--title);
  }
</style>
</head>
<body>
  <main class="canvas">
    <section class="book-cover">
      <p class="author-name">Marla Dovicki</p>
      <div class="bottle-artwork" role="img" aria-label="Row of overlapping translucent wine bottle silhouettes in muted slate, olive, wine, plum and blue tones"></div>
      <h1 class="book-title">GlassHaven</h1>
    </section>
  </main>
</body>
</html>
```